Pellham Grove Trust - New Website Designed

I need a site that looks like this http://www.quorlandgiving.org for boat donations. So please replace the cars with boats.

```html
<!DOCTYPE html>
<html lang="en">
<head>
<meta charset="utf-8">
<title>Pellham Grove Trust – Donate Your Boat</title>
<link href="https://fonts.googleapis.com/css2?family=Nunito+Sans:wght@400;600;700;800&family=Open+Sans:wght@400;600;700&display=swap" rel="stylesheet">
<style>
:root{
  --blue:#1fa9e1;
  --red:#e8304c;
  --ink:#222428;
  --text:#555a60;
  --muted:#8a8f95;
  --line:#e2e4e6;
  --soft:#f3f3f4;
  --white:#ffffff;
}
*{box-sizing:border-box;margin:0;padding:0}
html,body{width:1200px;height:2778px;overflow:hidden;background:var(--white)}
body{font-family:"Open Sans",sans-serif;color:var(--text);position:relative}
.abs{position:absolute}
h1,h2,h3,h4{font-family:"Nunito Sans",sans-serif;color:var(--ink)}

/* header */
.site-header{position:absolute;left:0;top:0;width:1200px;height:106px;background:var(--white)}
.brand{left:132px;top:32px;display:flex;align-items:center;gap:12px}
.brand-mark{width:30px;height:30px;border-radius:50%;background:var(--red)}
.brand-name{font-family:"Nunito Sans",sans-serif;font-weight:800;font-size:28px;color:var(--ink);letter-spacing:.2px}
.call-box{left:739px;top:0;width:329px;height:106px;background:var(--red);color:var(--white);display:flex;align-items:center;padding-left:22px;gap:18px}
.call-icon{width:50px;height:50px;border:2.5px solid var(--white);border-radius:50%;display:flex;align-items:center;justify-content:center}
.call-lines{font-family:"Nunito Sans",sans-serif}
.call-lines .lead{font-size:14px;font-weight:700;letter-spacing:.3px}
.call-lines .number{font-size:28px;font-weight:800;line-height:1.1}
.call-lines .note{font-size:9px;font-weight:700;letter-spacing:.2px}

.main-nav{position:absolute;left:0;top:106px;width:1200px;height:56px;background:var(--blue)}
.main-nav ul{list-style:none;display:flex;gap:40px;position:absolute;left:130px;top:19px}
.main-nav a{color:var(--white);text-decoration:none;font-size:13px;font-weight:600;font-family:"Open Sans",sans-serif}
.online-tab{left:730px;top:106px;width:338px;height:56px;background:var(--white);text-align:center;font-family:"Nunito Sans",sans-serif;font-weight:800;font-size:14px;color:var(--ink);line-height:56px;z-index:2}

/* hero */
.hero{position:absolute;left:0;top:162px;width:1200px;height:498px;
  background:linear-gradient(100deg,#6f7566 0%,#7e8a86 22%,#a9b9c6 42%,#c9d6e0 62%,#b6c6d2 80%,#98a9b6 100%)}
.slider-arrow{top:222px;width:42px;height:42px;border-radius:50%;background:rgba(40,40,40,.65);display:flex;align-items:center;justify-content:center}
.donate-form{left:739px;top:162px;width:329px;height:498px;background:var(--red);z-index:1}
.form-badge{left:140px;top:-10px;width:50px;height:50px;border-radius:50%;background:var(--white);display:flex;align-items:center;justify-content:center}
.form-title{top:62px;width:100%;text-align:center;color:var(--white);font-size:14px;font-weight:600}
.field{left:21px;width:286px;height:32px;background:var(--white);border-radius:2px;font-size:11px;color:#6a6a6a;padding-left:12px;line-height:32px}
.field.half{width:140px;display:flex;justify-content:space-between;padding-right:10px}
.btn-donate{left:84px;top:403px;width:160px;height:40px;background:var(--blue);color:var(--white);font-size:14px;font-weight:600;text-align:center;line-height:40px;border-radius:2px}

/* benefits */
.benefits{position:absolute;left:0;top:660px;width:1200px;height:308px;background:var(--soft)}
.benefits .kicker{top:42px;width:100%;text-align:center;font-family:"Nunito Sans",sans-serif;font-size:23px;color:var(--ink);font-weight:400}
.benefits .kicker span{color:var(--red)}
.benefits .headline{top:70px;width:100%;text-align:center;font-size:28px;font-weight:800}
.benefit{top:130px;width:200px;text-align:center;font-size:15px;color:var(--ink);line-height:24px}
.benefit svg{display:block;margin:0 auto 14px}
.shadow-rule{left:100px;top:968px;width:1000px;height:14px;background:radial-gradient(ellipse at top,rgba(0,0,0,.18),rgba(0,0,0,0) 70%)}

/* section heading with rules */
.sec-title{width:100%;text-align:center;font-size:27px;font-weight:800;display:flex;justify-content:center;align-items:center;gap:24px}
.sec-title::before,.sec-title::after{content:"";width:90px;height:1px;background:#bfc2c6}

.intro{top:1078px;left:270px;width:660px;text-align:center;font-size:11.5px;line-height:22px}
.step{top:1155px;width:330px;text-align:center}
.step .ring{width:152px;height:152px;border-radius:50%;border:1px solid var(--line);margin:0 auto;display:flex;align-items:center;justify-content:center}
.step h3{font-size:15px;font-weight:700;margin-top:24px}
.step p{font-size:11.5px;line-height:24px;margin-top:6px;padding:0 12px}
.step-divider{top:1195px;width:1px;height:222px;background:var(--line)}

/* why */
.why{position:absolute;left:0;top:1490px;width:1200px;height:448px;
  background:linear-gradient(90deg,#ffffff 0%,#f6f8f9 30%,#d9e7ee 48%,#a7c7d6 60%,#7fb3c7 72%,#6aa2b3 85%,#4d8ea2 100%)}
.why h2{left:132px;top:78px;font-size:26px;font-weight:800;display:flex;align-items:center;gap:14px}
.why h2::after{content:"";width:80px;height:1.5px;background:var(--red)}
.why ul{list-style:none;position:absolute;left:132px;top:136px;width:420px}
.why li{display:flex;gap:14px;margin-bottom:33px;font-size:12px;font-weight:700;color:var(--ink);line-height:24px}
.why .dot{flex:none;width:14px;height:14px;border-radius:50%;background:var(--blue);margin-top:5px;display:flex;align-items:center;justify-content:center}

/* faq */
.faq-photo{left:135px;top:2084px;width:340px;height:340px;border-radius:50%;border:6px solid #fff;box-shadow:0 0 0 1px var(--line),0 2px 8px rgba(0,0,0,.12);
  background:radial-gradient(circle at 55% 45%,#e9eef2 0%,#5d7da0 18%,#1c4270 45%,#132f55 100%)}
.faq-item{left:558px;width:510px;border:1px solid var(--line);background:#fff;padding:0 18px}
.faq-q{display:flex;justify-content:space-between;align-items:center;height:44px;font-size:14px;font-weight:600;color:var(--ink)}
.faq-q i{width:12px;height:12px;border:1px solid #b5b8bc;position:relative}
.faq-q i::before{content:"";position:absolute;left:2px;top:5px;width:6px;height:1px;background:#9a9ea3}
.faq-q i::after{content:"";position:absolute;left:5px;top:2px;width:1px;height:6px;background:#9a9ea3}
.faq-a{font-size:11px;line-height:22px;padding-bottom:14px}
.faq-a p+p{margin-top:8px}

/* footer */
.site-footer{position:absolute;left:0;top:2488px;width:1200px;height:290px;background:var(--soft)}
.foot-col{top:34px;font-size:11px;line-height:24px}
.foot-col h4{color:var(--blue);font-size:14px;font-weight:800;margin-bottom:12px}
.foot-col ul{list-style:none}
.newsletter p{line-height:24px;width:250px}
.mail-input{width:250px;height:40px;border:1px solid var(--line);background:#fff;margin-top:12px;padding-left:14px;line-height:38px;font-size:10px}
.btn-sub{margin-top:12px;width:90px;height:32px;background:var(--red);color:#fff;font-size:10px;font-weight:700;text-align:center;line-height:32px}
.contact li{display:flex;gap:14px;margin-bottom:4px}
.contact svg{flex:none;margin-top:7px}
.social li{display:flex;align-items:center;gap:10px;margin-bottom:8px}
.social .ring{width:32px;height:32px;border:1.5px solid #9a9ea3;border-radius:50%}
.foot-rule{left:132px;top:2730px;width:936px;height:1px;background:#d7d9dc}
.copyright{top:2744px;width:100%;text-align:center;font-size:11px}
.code{left:1078px;top:2744px;font-size:11px}
</style>
</head>
<body>

<header class="site-header">
  <div class="brand abs"><span class="brand-mark"></span><span class="brand-name">Pellham Grove Trust</span></div>
  <div class="call-box abs">
    <div class="call-icon"><svg width="24" height="24" viewBox="0 0 24 24"><path d="M6 3l3 4-2 2c1 3 4 6 7 7l2-2 4 3-2 4C10 21 3 14 2 5z" fill="none" stroke="#fff" stroke-width="2" stroke-linejoin="round"/></svg></div>
    <div class="call-lines">
      <div class="lead">CALL TODAY TO DONATE</div>
      <div class="number">1.888.888.8888</div>
      <div class="note">LIVE OPERATORS AVAILABLE – 7 DAYS A WEEK</div>
    </div>
  </div>
</header>

<nav class="main-nav">
  <ul>
    <li><a href="#">HOME</a></li><li><a href="#">ABOUT</a></li><li><a href="#">HOW TO DONATE</a></li>
    <li><a href="#">WHY DONNATE</a></li><li><a href="#">FAQ</a></li><li><a href="#">CONTACT</a></li>
  </ul>
</nav>
<div class="online-tab abs">DONATE YOUR BOAT ONLINE</div>

<section class="hero" role="img" aria-label="Photo of a soldier in uniform hugging a child wrapped in a flag at a harbour with white yachts">
  <div class="slider-arrow abs" style="left:66px"><svg width="14" height="14" viewBox="0 0 14 14"><path d="M9 2L4 7l5 5" fill="none" stroke="#fff" stroke-width="2.5"/></svg></div>
  <div class="slider-arrow abs" style="left:1092px"><svg width="14" height="14" viewBox="0 0 14 14"><path d="M5 2l5 5-5 5" fill="none" stroke="#fff" stroke-width="2.5"/></svg></div>
</section>

<form class="donate-form abs">
  <div class="form-badge abs"><span style="width:16px;height:16px;border-radius:50%;background:var(--red)"></span></div>
  <div class="form-title abs">Full Tax Deduction - Running or Not</div>
  <div class="field abs" style="top:109px">First Name</div>
  <div class="field abs" style="top:151px">Last Name</div>
  <div class="field abs" style="top:193px">Daytime Phone</div>
  <div class="field abs" style="top:234px">Email</div>
  <div class="field abs" style="top:276px">Zip Code</div>
  <div class="field half abs" style="top:318px">Choose Year<span>▾</span></div>
  <div class="field half abs" style="top:318px;left:167px">Choose Make<span>▾</span></div>
  <div class="field abs" style="top:359px">Boat Model</div>
  <div class="btn-donate abs">Donate Now</div>
</form>

<section class="benefits">
  <h2 class="kicker abs">DONATE YOUR BOAT TO <span>VETERANS</span></h2>
  <h2 class="headline abs">MAKE A DIFFERENCE</h2>
  <div class="benefit abs" style="left:76px">
    <svg width="60" height="64" viewBox="0 0 60 64" fill="none" stroke="#1fa9e1" stroke-width="2.5"><ellipse cx="20" cy="8" rx="14" ry="5"/><path d="M6 8v30c0 3 6 5 14 5M34 8v14M6 18c0 3 6 5 14 5s14-2 14-5M6 28c0 3 6 5 14 5"/><circle cx="40" cy="44" r="15"/><path d="M44 38h-6a3 3 0 000 6h4a3 3 0 010 6h-6M40 34v4M40 50v4"/></svg>
    You Have No<br>Costs</div>
  <div class="benefit abs" style="left:270px">
    <svg width="64" height="64" viewBox="0 0 64 64" fill="none" stroke="#1fa9e1" stroke-width="2.5"><rect x="4" y="18" width="34" height="26"/><path d="M38 26h12l8 10v8H38z"/><circle cx="16" cy="48" r="6"/><circle cx="48" cy="48" r="6"/></svg>
    Free Towing,<br>Running or Not</div>
  <div class="benefit abs" style="left:480px">
    <svg width="54" height="64" viewBox="0 0 54 64" fill="none" stroke="#1fa9e1" stroke-width="2.5"><path d="M6 2h42v60H6z"/><text x="27" y="18" font-size="13" font-family="Open Sans" fill="#1fa9e1" stroke="none" text-anchor="middle" font-weight="700">TAX</text><path d="M12 28h30M12 36h30M12 44h20M12 52h14"/></svg>
    We issue you an<br>IRS tax receipt</div>
  <div class="benefit abs" style="left:680px">
    <svg width="64" height="64" viewBox="0 0 64 64" fill="none" stroke="#1fa9e1" stroke-width="2.5"><path d="M6 8h36v52H6z"/><path d="M12 20h18M12 28h18M12 36h14M12 44h14"/><path d="M56 6l4 4-24 24-7 3 3-7z"/></svg>
    We take care of<br>all paperwork</div>
  <div class="benefit abs" style="left:896px">
    <svg width="60" height="64" viewBox="0 0 60 64" fill="none" stroke="#1fa9e1" stroke-width="2.5"><circle cx="30" cy="8" r="5"/><path d="M30 13v46M18 22h24M6 38c2 12 12 20 24 21 12-1 22-9 24-21M2 42l4-6 6 5M58 42l-4-6-6 5"/></svg>
    We take care of<br>DMV &amp; Smog issues</div>
</section>
<div class="shadow-rule abs"></div>

<h2 class="sec-title abs" style="top:1034px">HOW TO DONATE</h2>
<p class="intro abs">Lorem ipsum dolor sit amet, consectetur adipiscing elit, sed do eiusmod tempor incididunt ut labore et dolore magna aliqua sint occaecat cupidatat non proident, sunt in culpa qui officia</p>

<div class="step abs" style="left:105px">
  <div class="ring"><svg width="64" height="74" viewBox="0 0 64 74" fill="none" stroke="#e8304c" stroke-width="2.5"><rect x="18" y="6" width="28" height="62" rx="4"/><path d="M18 16h28M18 56h28"/><circle cx="32" cy="62" r="2"/><path d="M10 24c-4 6-4 14 0 20M4 20c-6 9-6 19 0 28M54 24c4 6 4 14 0 20M60 20c6 9 6 19 0 28"/></svg></div>
  <h3>CALL US</h3>
  <p>Nostrud exercitation ullamco laboris nisi ut aliquip ex ea commodo consequat. Duis aute irure dolor in reprehenderit in voluptate velit...</p>
</div>
<div class="step-divider abs" style="left:436px"></div>
<div class="step abs" style="left:435px">
  <div class="ring"><svg width="72" height="64" viewBox="0 0 72 64" fill="none" stroke="#e8304c" stroke-width="2.5"><rect x="6" y="18" width="38" height="28"/><path d="M44 28h14l8 10v8H44z"/><circle cx="18" cy="50" r="6"/><circle cx="54" cy="50" r="6"/><path d="M2 58h68"/></svg></div>
  <h3>WE TOW THE BOAT</h3>
  <p>Nostrud exercitation ullamco laboris nisi ut aliquip ex ea commodo consequat. Duis aute irure dolor in reprehenderit in voluptate velit...</p>
</div>
<div class="step-divider abs" style="left:764px"></div>
<div class="step abs" style="left:767px">
  <div class="ring"><svg width="64" height="64" viewBox="0 0 64 64" fill="none" stroke="#e8304c" stroke-width="3" stroke-linejoin="round"><path d="M46 6l12 12-36 36-16 4 4-16z"/><path d="M40 12l12 12M10 42l12 12"/></svg></div>
  <h3>TAX WRITE-OFF</h3>
  <p>Nostrud exercitation ullamco laboris nisi ut aliquip ex ea commodo consequat. Duis aute irure dolor in reprehenderit in voluptate velit...</p>
</div>

<section class="why" role="img" aria-label="Photo of a large white motor yacht moored in a marina with green hills behind">
  <h2 class="abs">WHY DONATE YOUR BOAT TO US</h2>
  <ul>
    <li><span class="dot"><svg width="6" height="8" viewBox="0 0 6 8"><path d="M1 1l3 3-3 3" fill="none" stroke="#fff" stroke-width="1.6"/></svg></span>Lorem ipsum dolor sit amet, consectetur adipiscing elit, sed do eiusmod tempor incididunt ut labor</li>
    <li><span class="dot"><svg width="6" height="8" viewBox="0 0 6 8"><path d="M1 1l3 3-3 3" fill="none" stroke="#fff" stroke-width="1.6"/></svg></span>Lorem ipsum dolor sit amet, consectetur adipiscing elit, sed do eiusmod tempor incididunt ut labor</li>
    <li><span class="dot"><svg width="6" height="8" viewBox="0 0 6 8"><path d="M1 1l3 3-3 3" fill="none" stroke="#fff" stroke-width="1.6"/></svg></span>Lorem ipsum dolor sit amet, consectetur adipiscing elit, sed do eiusmod tempor incididunt ut labor</li>
    <li><span class="dot"><svg width="6" height="8" viewBox="0 0 6 8"><path d="M1 1l3 3-3 3" fill="none" stroke="#fff" stroke-width="1.6"/></svg></span>Lorem ipsum dolor sit amet, consectetur adipiscing elit, sed do eiusmod tempor incididunt ut labor</li>
  </ul>
</section>

<h2 class="sec-title abs" style="top:2004px">FAQ</h2>
<div class="faq-photo abs" role="img" aria-label="Aerial photo of a speedboat cutting through deep blue water"></div>
<div class="faq-item abs" style="top:2086px">
  <div class="faq-q">Eiusmod tempor incididunt ut labore et dolore magna aliqua ?<i></i></div>
  <div class="faq-a">
    <p>Accusantium doloremque laudantium, totam rem aperiam, eaque ipsa quae ab illo inventore veritatis et quasi architecto beatae vitae dicta sunt explicabo...</p>
    <p>Doloremque laudantium, totam rem aperiam, eaque ipsa quae ab illo inventore veritatis et quasi architecto beatae vitae dicta sunt explicabo...</p>
  </div>
</div>
<div class="faq-item abs" style="top:2256px"><div class="faq-q">Eiusmod tempor incididunt ut labore et dolore magna aliqua ?<i></i></div></div>
<div class="faq-item abs" style="top:2311px"><div class="faq-q">Eiusmod tempor incididunt ut labore et dolore magna aliqua ?<i></i></div></div>
<div class="faq-item abs" style="top:2367px"><div class="faq-q">Eiusmod tempor incididunt ut labore et dolore magna aliqua ?<i></i></div></div>

<footer class="site-footer">
  <div class="foot-col abs" style="left:132px">
    <h4>QUICK LINKS</h4>
    <ul><li>Home</li><li>About</li><li>How to Donate</li><li>Why Donate</li><li>FAQ</li><li>Contact us</li></ul>
  </div>
  <div class="foot-col newsletter abs" style="left:336px">
    <h4>NEWSLETTER</h4>
    <p>Enter your email address to receive the latest news and notes from our blog.</p>
    <div class="mail-input">Enter Your Mail Id</div>
    <div class="btn-sub">SUBSCRIBE</div>
  </div>
  <div class="foot-col contact abs" style="left:706px">
    <h4>CONTACT US</h4>
    <ul>
      <li><svg width="12" height="10" viewBox="0 0 12 10"><path d="M1 3c3-3 7-3 10 0l-2 2-1-1H4L3 5zM3 6h6v3H3z" fill="#6d7176"/></svg>(215) 555-0142</li>
      <li><svg width="12" height="10" viewBox="0 0 12 10"><path d="M3 0h6v3H3zM1 3h10v5H9v2H3V8H1z" fill="#6d7176"/></svg>(215) 555-0142</li>
      <li><svg width="12" height="10" viewBox="0 0 12 10"><path d="M0 1h12v8H0z" fill="#6d7176"/><path d="M0 1l6 4 6-4" fill="none" stroke="#fff"/></svg><u>info@pellhamgrove.org</u></li>
      <li><svg width="12" height="12" viewBox="0 0 12 12"><path d="M6 0a4 4 0 014 4c0 3-4 8-4 8S2 7 2 4a4 4 0 014-4z" fill="#6d7176"/><circle cx="6" cy="4" r="1.5" fill="#f3f3f4"/></svg><span style="line-height:16px;padding-top:4px">#2868 Lorem ipsum dolor sit<br>amet, consectetur</span></li>
    </ul>
  </div>
  <div class="foot-col social abs" style="left:980px">
    <h4>FOLLOW US</h4>
    <ul><li><span class="ring"></span>Friendpage</li><li><span class="ring"></span>Chirpline</li><li><span class="ring"></span>Workring</li></ul>
  </div>
</footer>
<div class="foot-rule abs"></div>
<div class="copyright abs">©2017 Pellham Grove Trust | all rights reserved</div>
<div class="code abs">C11</div>

</body>
</html>
```